Harborline Auto LLC

Car Dealer Customer Service
Address: 2874 Cresthaven Road, Shelbyville, TN 37162
web: www.harborlineautoxq.net
email: harborlineautoxq@mailnest.example
Phone: (931) 555-0148
Phone: (629) 555-0173

```html
<!DOCTYPE html>
<html lang="en">
<head>
<meta charset="utf-8">
<title>Harborline Auto – Business Card</title>
<link rel="stylesheet" href="https://fonts.googleapis.com/css2?family=Montserrat:wght@400;500;800&display=swap">
<style>
  :root {
    --bg: #e9eaec;
    --card: #ffffff;
    --blue: #1f78b4;
    --blue-band: #2a8bc9;
    --gold: #e8b13b;
    --ink: #1b1b1b;
  }
  * { box-sizing: border-box; margin: 0; padding: 0; }
  html, body { width: 1200px; height: 900px; overflow: hidden; }
  body {
    background: var(--bg);
    font-family: "Montserrat", Arial, sans-serif;
    display: flex;
    flex-direction: column;
    align-items: center;
    justify-content: center;
    gap: 40px;
  }
  .card {
    position: relative;
    width: 680px;
    height: 389px;
    background: var(--card);
    box-shadow: 0 6px 18px rgba(0,0,0,0.12);
  }
  .brand {
    display: flex;
    align-items: center;
    gap: 14px;
    color: var(--blue);
    font-weight: 800;
    text-transform: uppercase;
    letter-spacing: 0.5px;
  }
  .brand-dot {
    flex: none;
    border-radius: 50%;
    background: var(--blue);
  }
  /* Front */
  .card-front { display: flex; align-items: center; justify-content: center; }
  .card-front .brand { font-size: 38px; }
  .card-front .brand-dot { width: 44px; height: 44px; }
  /* Back */
  .card-back .brand {
    position: absolute;
    left: 40px;
    top: 148px;
    font-size: 22px;
    line-height: 1.15;
    gap: 12px;
  }
  .card-back .brand-dot { width: 30px; height: 30px; }
  .divider {
    position: absolute;
    left: 300px;
    top: 105px;
    width: 2px;
    height: 135px;
    background: var(--blue);
  }
  .contacts {
    position: absolute;
    left: 326px;
    top: 108px;
    list-style: none;
    display: flex;
    flex-direction: column;
    gap: 12px;
    font-size: 15px;
    color: var(--ink);
  }
  .contacts li { display: flex; align-items: center; gap: 10px; white-space: nowrap; }
  .contacts svg { width: 16px; height: 16px; flex: none; fill: var(--blue); }
  .contacts .accent { color: var(--blue); }
  .bands { position: absolute; left: 0; bottom: 22px; width: 680px; height: 44px; }
  .bands svg { position: absolute; inset: 0; }
  .band-text {
    position: absolute;
    top: 0;
    height: 44px;
    display: flex;
    align-items: center;
    font-size: 15px;
    font-weight: 500;
    color: #ffffff;
  }
  .band-address { left: 28px; }
  .band-service { left: 472px; }
</style>
</head>
<body>
  <section class="card card-front">
    <div class="brand"><span class="brand-dot"></span>Harborline Auto</div>
  </section>

  <section class="card card-back">
    <div class="brand"><span class="brand-dot"></span>Harborline<br>Auto</div>
    <div class="divider"></div>
    <ul class="contacts">
      <li>
        <svg viewBox="0 0 24 24" aria-hidden="true"><path d="M6.6 10.8a15.1 15.1 0 0 0 6.6 6.6l2.2-2.2a1 1 0 0 1 1-.25 11.4 11.4 0 0 0 3.6.57 1 1 0 0 1 1 1V20a1 1 0 0 1-1 1A17 17 0 0 1 3 4a1 1 0 0 1 1-1h3.5a1 1 0 0 1 1 1c0 1.25.2 2.45.57 3.57a1 1 0 0 1-.25 1z"/></svg>
        (931) 555-0148
      </li>
      <li>
        <svg viewBox="0 0 24 24" aria-hidden="true"><path d="M6.6 10.8a15.1 15.1 0 0 0 6.6 6.6l2.2-2.2a1 1 0 0 1 1-.25 11.4 11.4 0 0 0 3.6.57 1 1 0 0 1 1 1V20a1 1 0 0 1-1 1A17 17 0 0 1 3 4a1 1 0 0 1 1-1h3.5a1 1 0 0 1 1 1c0 1.25.2 2.45.57 3.57a1 1 0 0 1-.25 1z"/></svg>
        (629) 555-0173
      </li>
      <li>
        <svg viewBox="0 0 24 24" aria-hidden="true"><path d="M2 5h20v14H2z M3.5 6.5 12 13l8.5-6.5" fill="var(--blue)" stroke="#fff" stroke-width="1.4"/></svg>
        harborlineautoxq@mailnest.example
      </li>
      <li>
        <svg viewBox="0 0 24 24" aria-hidden="true"><circle cx="12" cy="12" r="10"/><path d="M2 12h20M12 2c3 3 3 17 0 20M12 2c-3 3-3 17 0 20" fill="none" stroke="#fff" stroke-width="1.3"/></svg>
        <span>www.<span class="accent">harborlineautoxq</span>.net</span>
      </li>
    </ul>
    <div class="bands">
      <svg viewBox="0 0 680 44" aria-hidden="true">
        <polygon points="0,0 458,0 446,44 0,44" fill="var(--blue-band)"/>
        <polygon points="466,0 660,0 660,44 454,44" fill="var(--gold)"/>
      </svg>
      <div class="band-text band-address">2874 Cresthaven Road, Shelbyville, TN 37162</div>
      <div class="band-text band-service">Car Dealer Customer Service</div>
    </div>
  </section>
</body>
</html>
```